Eyecatching Carpentry Business card

I need a business card designed for myself, my company name is Tom Hadley Carpentry.
I am based on the south coast of England and I do all aspects of carpentry, including;
skirting
Architraves
kitchens
roof construction
flooring
doors
loft conversions
decking
windows
I currently have no company logo or letter head so I leave all design ideas to designers.
All I ask is that it looks professional and modern.
A logo may be incorporated as well.
My contact details should be on the back, telephone and email.

```html
<!DOCTYPE html>
<html lang="en">
<head>
<meta charset="utf-8">
<title>Tom Hadley Carpentry – Business Card</title>
<link rel="stylesheet" href="https://fonts.googleapis.com/css2?family=Didact+Gothic&family=Michroma&family=Oswald:wght@500&display=swap">
<style>
  :root {
    --backdrop: #2f2f31;
    --card-white: #ffffff;
    --panel-grey: #f1f1f1;
    --ink-grey: #5a5a5a;
    --ink-dark: #4a4a4a;
    --accent-red: #8b1c1c;
    --dot-grey: #8a8a8a;
  }
  * { box-sizing: border-box; margin: 0; padding: 0; }
  html, body {
    width: 1200px;
    height: 816px;
    overflow: hidden;
    background: var(--backdrop);
  }
  .card {
    position: absolute;
    left: 100px;
    top: 118px;
    width: 1000px;
    height: 580px;
    border-radius: 44px;
    background: var(--card-white);
    overflow: hidden;
  }
  .contact-panel {
    position: absolute;
    inset: 0;
    background: var(--panel-grey);
    clip-path: polygon(47% 0, 100% 0, 100% 100%, 56% 100%, 53% 62%, 51.5% 60%, 53% 58.5%);
  }
  .brand {
    position: absolute;
    left: 80px;
    top: 270px;
    display: flex;
    flex-direction: column;
    align-items: flex-start;
    gap: 22px;
  }
  .brand-mark {
    width: 62px;
    height: 62px;
    border-radius: 12px;
    background: var(--accent-red);
  }
  .brand-name {
    font-family: "Didact Gothic", sans-serif;
    font-size: 66px;
    color: var(--ink-grey);
    letter-spacing: 1px;
  }
  .contact-list {
    position: absolute;
    left: 560px;
    top: 82px;
    list-style: none;
    font-family: "Michroma", sans-serif;
    font-size: 15px;
    color: var(--ink-dark);
    letter-spacing: 1.5px;
  }
  .contact-item {
    display: flex;
    align-items: flex-start;
    gap: 12px;
    margin-bottom: 22px;
    line-height: 1.6;
  }
  .contact-icon {
    flex: none;
    width: 16px;
    height: 16px;
    margin-top: 3px;
    fill: var(--accent-red);
  }
  .divider {
    position: absolute;
    border-top: 3px dotted var(--dot-grey);
  }
  .divider-upper { left: 640px; top: 300px; width: 290px; }
  .divider-lower { left: 560px; top: 392px; width: 250px; }
  .person {
    position: absolute;
    right: 70px;
    top: 372px;
    text-align: right;
    font-family: "Oswald", sans-serif;
    font-weight: 500;
    color: var(--ink-grey);
    text-transform: uppercase;
  }
  .person-name { font-size: 44px; letter-spacing: 1px; line-height: 1.1; }
  .person-role { font-size: 24px; letter-spacing: 1px; }
</style>
</head>
<body>
  <main class="card">
    <div class="contact-panel"></div>

    <div class="brand">
      <div class="brand-mark"></div>
      <div class="brand-name">Tom Hadley</div>
    </div>

    <ul class="contact-list">
      <li class="contact-item">
        <svg class="contact-icon" viewBox="0 0 16 16" aria-hidden="true"><path d="M3 1h3l1 4-2 1c1 2 3 4 5 5l1-2 4 1v3c0 1-1 2-2 2C7 15 1 9 1 3c0-1 1-2 2-2z"/></svg>
        <span>+44 (0123) 45-678-90</span>
      </li>
      <li class="contact-item">
        <svg class="contact-icon" viewBox="0 0 16 16" aria-hidden="true"><path d="M1 3h14v10H1z M1 3l7 6 7-6" stroke="#f1f1f1" stroke-width="1.2"/></svg>
        <span>hello@tomhadley.co.uk</span>
      </li>
      <li class="contact-item">
        <svg class="contact-icon" viewBox="0 0 16 16" aria-hidden="true"><circle cx="8" cy="8" r="7"/><path d="M1 8h14M8 1v14M3 4h10M3 12h10" stroke="#f1f1f1" stroke-width="1" fill="none"/><ellipse cx="8" cy="8" rx="3.5" ry="7" stroke="#f1f1f1" stroke-width="1" fill="none"/></svg>
        <span>www.tomhadley.co.uk</span>
      </li>
      <li class="contact-item">
        <svg class="contact-icon" viewBox="0 0 16 16" aria-hidden="true"><path d="M8 1l7 7h-2v7H9v-4H7v4H3V8H1z"/></svg>
        <span>14 Harbour Lane,<br>Southsea, England</span>
      </li>
    </ul>

    <div class="divider divider-upper"></div>
    <div class="divider divider-lower"></div>

    <div class="person">
      <div class="person-name">Daniel Marsh</div>
      <div class="person-role">General Manager</div>
    </div>
  </main>
</body>
</html>
```